Refresh Brightpath Coursecraft

Need a new design for e-learning development and web app development site: http://brightpathcoursecraft.example. Need pages for everything on menu bar plus a training services and a web app development services pages and a better page for samples http://brightpathcoursecraft.example/samples5/.

***Must be programmed in html 5. NO CMS. No WP. No Plume. Straight html/css.

Target Market(s)

government

Industry/Entity Type

Government

Coding

Coded - Design and coding required

Number of Pages Required

1 page

Requirements
Must have
• Must be coded in html5/css. No CMS.
• Divided so you can easily see that we offer 3 separate services:
• Live Training - E-Learning Development - Web App Development
• A way to display logos of all our clients like on bottom of this page: https://www.quorvatests.example (this is also our website so you can copy all these logos)
• List both our Denver location which is already on our website plus our office in Velmoro Plaza. Street 62 Sur, 14-87. Medellín, Antioquia.
• A page like this for our web app dev services https://www.tekvanu.example/product-development
Should not have
• CMS

```html
<!DOCTYPE html>
<html lang="en">
<head>
<meta charset="utf-8">
<title>Brightpath Coursecraft</title>
<link href="https://fonts.googleapis.com/css2?family=Josefin+Sans:wght@600;700&family=Mulish:wght@400;600;700&display=swap" rel="stylesheet">
<style>
:root{
  --orange:#f7a12b;
  --orange-dark:#ef9416;
  --blue:#1b6fb0;
  --blue-deep:#1e5f96;
  --ink:#222428;
  --body:#555a60;
  --line:#d9d9d9;
  --paper:#ffffff;
  --mist:#f0f1f3;
}
*{box-sizing:border-box;margin:0;padding:0}
html,body{width:1200px;height:4000px;overflow:hidden;background:var(--paper)}
body{position:relative;font-family:"Mulish",sans-serif;color:var(--ink)}
.abs{position:absolute}

/* top bar */
.topbar{left:0;top:0;width:1200px;height:43px;background:var(--orange);color:#fff;font-size:14px;font-weight:600;display:flex;align-items:center;justify-content:flex-end;padding-right:112px;gap:10px}
.nav{left:0;top:43px;width:1200px;height:90px;background:#fff;display:flex;align-items:center;padding:0 112px;justify-content:space-between}
.brand{display:flex;align-items:center;gap:12px}
.brand-dot{width:34px;height:34px;border-radius:50%;background:var(--blue)}
.brand-name{font-size:22px;font-weight:700;color:var(--blue);line-height:1}
.menu{display:flex;gap:58px;font-size:15px;font-weight:600;letter-spacing:.5px;text-transform:uppercase}

/* hero */
.hero{left:0;top:133px;width:1200px;height:590px;background:linear-gradient(120deg,#9a6b4f 0%,#c8a48c 35%,#e6ddd6 60%,#b7b0ad 100%)}
.hero-title{left:0;top:278px;width:1200px;text-align:center;font-family:"Josefin Sans",sans-serif;font-weight:700;font-size:70px;line-height:76px;color:#fff;letter-spacing:3px;text-transform:uppercase}
.hero-dots{left:0;top:516px;width:1200px;display:flex;justify-content:center;gap:20px}
.hero-dots span{width:18px;height:18px;border-radius:50%;border:2px solid #fff}
.hero-dots span.on{background:#fff}
.hero-curve{left:0;top:560px}
.mouse{left:586px;top:635px}

/* offer */
.section-title{left:0;width:1200px;text-align:center;font-size:44px;font-weight:400;color:var(--ink)}
.service-media{width:426px;height:360px}
.service-media .frame-o{position:absolute;left:-10px;top:-10px;width:426px;height:352px;background:var(--orange)}
.service-media .frame-b{position:absolute;left:12px;top:12px;width:426px;height:352px;background:var(--blue)}
.service-media .photo{position:absolute;left:0;top:0;width:426px;height:352px}
.service-media .badge{position:absolute;top:130px;width:104px;height:104px;border-radius:50%;background:var(--blue);border:6px solid #fff;box-shadow:0 0 0 2px var(--blue);display:flex;align-items:center;justify-content:center}
.service-text{width:420px}
.service-text h2{font-size:36px;font-weight:600;color:var(--blue);text-transform:uppercase;line-height:40px}
.service-text h3{font-size:21px;font-weight:600;color:var(--ink);margin-top:6px}
.service-text p{font-size:15px;line-height:30px;color:var(--body);margin-top:24px}
.btn{display:inline-block;margin-top:34px;background:var(--orange);color:#fff;font-size:16px;font-weight:700;border-radius:26px;padding:12px 30px}

/* clients */
.clients{left:120px;top:2613px;width:960px}
.client-row{display:flex}
.client{width:160px;height:84px;border:1px solid var(--line);margin:-1px 0 0 -1px;display:flex;align-items:center;justify-content:center;gap:8px;font-size:15px;font-weight:700;color:#6a6e73;text-align:center;padding:0 8px;line-height:1.2}
.client .seal{width:56px;height:56px;border-radius:50%;background:#d4d6d8}
.client .mark{width:14px;height:14px;border-radius:50%;background:#9aa0a6;flex:none}
.client-row.last{justify-content:center}

/* newsletter */
.band{left:0;top:3115px;width:1200px;height:405px;background:linear-gradient(100deg,#2f6f9c 0%,#5d93b8 45%,#9cbbd0 100%)}
.tile{width:163px;height:139px;color:#fff;display:flex;flex-direction:column;align-items:center;justify-content:center;gap:14px;font-size:15px;font-weight:600}
.tile.blue{background:var(--blue)}
.tile.orange{background:var(--orange)}
.newsletter{left:459px;top:3179px;width:626px;height:282px;background:var(--orange);padding:40px 52px;color:#fff}
.newsletter h2{font-size:32px;font-weight:400}
.newsletter p{font-size:13px;line-height:22px;margin-top:18px;width:430px}
.newsletter .field{margin-top:20px;height:48px;background:#fff;color:#888;font-size:14px;display:flex;align-items:center;padding-left:22px}
.newsletter .send{margin-top:12px;font-size:13px;font-weight:700;text-decoration:underline}

/* footer */
.footer{left:0;top:3520px;width:1200px;height:350px;background:var(--mist)}
.foot-h{font-size:21px;font-weight:600;text-transform:uppercase;color:var(--ink)}
.foot-p{font-size:14px;line-height:26px;color:var(--body)}
.social{display:flex;gap:10px}
.social span{font-size:11px;font-weight:600;color:var(--body);border:1px solid #8b8f94;border-radius:14px;padding:4px 9px}
.contact-line{display:flex;gap:20px;font-size:14px;color:var(--body);line-height:26px;margin-bottom:18px}
.contact-line svg{flex:none;margin-top:5px}
.map{left:765px;top:3619px;width:323px;height:221px;background:linear-gradient(135deg,#e9e4d8 0%,#dfe6d6 50%,#a9c8e6 100%);border:1px solid #ccc}
.foot-nav{left:0;top:3872px;width:1200px;height:48px;display:flex;justify-content:center;align-items:center;gap:40px;font-size:13px;font-weight:600;text-transform:uppercase;color:var(--ink);border-top:1px solid var(--line)}
.bottombar{left:0;top:3920px;width:1200px;height:80px;background:var(--blue);color:#fff;font-size:14px;display:flex;align-items:center;justify-content:center}
</style>
</head>
<body>

<div class="abs topbar">
  <svg width="14" height="18" viewBox="0 0 14 18"><path d="M7 0C3 0 0 3 0 7c0 5 7 11 7 11s7-6 7-11c0-4-3-7-7-7zm0 10a3 3 0 110-6 3 3 0 010 6z" fill="#fff"/></svg>
  <span>5830 E Larkspur Avenue, Suite 2-140, Aurora, CO 80012</span>
</div>

<header class="abs nav">
  <div class="brand"><span class="brand-dot"></span><span class="brand-name">Brightpath Coursecraft</span></div>
  <nav class="menu"><span>Home</span><span>Portfolio</span><span>Team &amp; Experience</span><span>Contact</span></nav>
</header>

<div class="abs hero" role="img" aria-label="Person writing in a notebook beside a laptop on a desk"></div>
<h1 class="abs hero-title">Brightpath Coursecraft<br>Solutions</h1>
<div class="abs hero-dots"><span class="on"></span><span></span><span></span><span></span></div>
<svg class="abs hero-curve" width="1200" height="170" viewBox="0 0 1200 170" preserveAspectRatio="none"><path d="M0 170 L0 160 Q600 30 1200 40 L1200 170 Z" fill="#fff"/></svg>
<svg class="abs mouse" width="28" height="72" viewBox="0 0 28 72"><rect x="2" y="2" width="24" height="38" rx="12" fill="#fff" stroke="#b9bcc0" stroke-width="2"/><line x1="14" y1="10" x2="14" y2="18" stroke="#b9bcc0" stroke-width="3" stroke-linecap="round"/><path d="M8 50l6 6 6-6M8 60l6 6 6-6" fill="none" stroke="#b9bcc0" stroke-width="2"/></svg>

<h2 class="abs section-title" style="top:820px">What We Offer</h2>

<!-- Live training -->
<div class="abs service-media" style="left:117px;top:938px">
  <div class="frame-o"></div><div class="frame-b"></div>
  <div class="photo" role="img" aria-label="Student studying at a laptop in a home setting" style="background:linear-gradient(135deg,#b8875f,#e2c39e 50%,#7d5b45)"></div>
  <div class="badge" style="left:372px"><svg width="48" height="40" viewBox="0 0 48 40"><rect x="6" y="3" width="36" height="24" rx="2" fill="none" stroke="#fff" stroke-width="3"/><path d="M2 32h44" stroke="#fff" stroke-width="3"/></svg></div>
</div>
<div class="abs service-text" style="left:667px;top:950px">
  <h2>Live Training</h2>
  <h3>Lorem ipsum dolor sit ame</h3>
  <p>Lorem ipsum dolor sit amet, consectetur adipiscing elit, sed do eiusmod tempor incididunt ut labore et dolore magna aliqua. Ut enim ad minim veniam, quitrudquat. Duis aute irure dolor in reprehenderit in voluptate velit esse cillum dolore eu fugiat nulla pariatur.</p>
  <span class="btn">Read More</span>
</div>

<!-- E-learning development -->
<div class="abs service-text" style="left:110px;top:1465px;width:470px">
  <h2>E-Learning Development</h2>
  <h3>Lorem ipsum dolor sit ame</h3>
  <p>Lorem ipsum dolor sit amet, consectetur adipiscing elit, sed do eiusmod tempor incididunt ut labore et dolore magna aliqua. Ut enim ad minim veniam, quitrudquat. Duis aute irure dolor in reprehenderit in voluptate velit esse cillum dolore eu fugiat nulla pariatur.</p>
  <span class="btn">Read More</span>
</div>
<div class="abs service-media" style="left:665px;top:1450px">
  <div class="frame-o" style="left:10px"></div><div class="frame-b" style="left:-4px"></div>
  <div class="photo" role="img" aria-label="Woman working at a laptop in a bright office" style="background:linear-gradient(135deg,#e8e4de,#9b918a 55%,#4d4a48)"></div>
  <div class="badge" style="left:-52px"><svg width="48" height="40" viewBox="0 0 48 40"><rect x="6" y="3" width="36" height="24" rx="2" fill="none" stroke="#fff" stroke-width="3"/><path d="M2 32h44" stroke="#fff" stroke-width="3"/></svg></div>
</div>

<!-- Web app development -->
<div class="abs service-media" style="left:117px;top:1970px">
  <div class="frame-o"></div><div class="frame-b"></div>
  <div class="photo" role="img" aria-label="Desktop monitor showing an online learning screen" style="background:linear-gradient(135deg,#e4e6e8,#bfc3c7 55%,#8a8f94)"></div>
  <div class="badge" style="left:372px"><svg width="44" height="44" viewBox="0 0 44 44"><rect x="4" y="6" width="36" height="28" rx="2" fill="none" stroke="#fff" stroke-width="3"/><rect x="24" y="16" width="12" height="22" rx="2" fill="var(--blue)" stroke="#fff" stroke-width="3"/></svg></div>
</div>
<div class="abs service-text" style="left:667px;top:1978px">
  <h2>Web App Development</h2>
  <h3>Lorem ipsum dolor sit ame</h3>
  <p>Lorem ipsum dolor sit amet, consectetur adipiscing elit, sed do eiusmod tempor incididunt ut labore et dolore magna aliqua. Ut enim ad minim veniam, quitrudquat. Duis aute irure dolor in reprehenderit in voluptate velit esse cillum dolore eu fugiat nulla pariatur.</p>
  <span class="btn">Read More</span>
</div>

<h2 class="abs section-title" style="top:2510px">Our Clients</h2>
<div class="abs clients">
  <div class="client-row">
    <div class="client">Northwind Aviation Corps</div>
    <div class="client">Corvale University</div>
    <div class="client"><span class="seal"></span></div>
    <div class="client">Trailstead Works</div>
    <div class="client"><span class="seal"></span></div>
    <div class="client">Meridane</div>
  </div>
  <div class="client-row">
    <div class="client"><span class="mark"></span>Solvanta</div>
    <div class="client"><span class="seal"></span></div>
    <div class="client"><span class="seal"></span></div>
    <div class="client">Ashcombe</div>
    <div class="client">University of Greyhollow</div>
    <div class="client"><span class="seal"></span></div>
  </div>
  <div class="client-row">
    <div class="client"><span class="seal"></span></div>
    <div class="client"><span class="seal"></span></div>
    <div class="client">Pellham State</div>
    <div class="client">Ridgeline U</div>
    <div class="client"><span class="seal"></span></div>
    <div class="client"><span class="seal"></span></div>
  </div>
  <div class="client-row last">
    <div class="client"><span class="seal"></span></div>
    <div class="client">Quillor</div>
    <div class="client">Ostelia Labs</div>
  </div>
</div>

<!-- newsletter band -->
<div class="abs band" role="img" aria-label="Blue toned photo of a person working at a desk"></div>
<div class="abs tile blue" style="left:112px;top:3179px">
  <svg width="56" height="50" viewBox="0 0 56 50"><circle cx="28" cy="16" r="10" fill="none" stroke="#fff" stroke-width="3"/><circle cx="28" cy="16" r="3" fill="#fff"/><path d="M8 46c2-10 10-14 20-14s18 4 20 14" fill="none" stroke="#fff" stroke-width="3"/></svg>
  <span>Our Services</span>
</div>
<div class="abs tile orange" style="left:284px;top:3179px">
  <svg width="56" height="50" viewBox="0 0 56 50"><circle cx="28" cy="24" r="19" fill="none" stroke="#fff" stroke-width="3"/><text x="28" y="30" text-anchor="middle" font-family="Mulish,sans-serif" font-size="15" font-weight="700" fill="#fff">24</text></svg>
  <span>Support</span>
</div>
<div class="abs tile orange" style="left:112px;top:3322px">
  <svg width="56" height="44" viewBox="0 0 56 44"><rect x="3" y="6" width="50" height="34" fill="none" stroke="#fff" stroke-width="3"/><path d="M3 6l25 20 25-20" fill="none" stroke="#fff" stroke-width="3"/></svg>
  <span>Email Services</span>
</div>
<div class="abs tile blue" style="left:284px;top:3322px">
  <svg width="44" height="44" viewBox="0 0 24 24"><path d="M6.6 10.8a15 15 0 006.6 6.6l2.2-2.2c.3-.3.7-.4 1-.2 1.1.4 2.3.6 3.6.6.6 0 1 .4 1 1V20c0 .6-.4 1-1 1A17 17 0 013 4c0-.6.4-1 1-1h3.5c.6 0 1 .4 1 1 0 1.3.2 2.5.6 3.6.1.3 0 .7-.2 1z" fill="none" stroke="#fff" stroke-width="1.4"/></svg>
  <span>+1 888 555 0147</span>
</div>
<div class="abs newsletter">
  <h2>Subscribe Our Newsletter</h2>
  <p>Sed ut perspiciatis unde omnis iste natus error sit voluptatem accusantium doloremque laudantium.</p>
  <div class="field">Enter Your Email Address</div>
  <div class="send">SEND</div>
</div>

<!-- footer -->
<div class="abs footer"></div>
<div class="abs" style="left:112px;top:3606px;width:300px">
  <div class="foot-h">Office Address</div>
  <p class="foot-p" style="margin-top:18px">Velmoro Plaza. Street 62 Sur, 14-87.<br>Medellín, Antioquia</p>
  <div class="social" style="margin-top:22px"><span>Kavo</span><span>Lumet</span><span>Ostra</span><span>Pinel</span></div>
</div>
<div class="abs" style="left:443px;top:3606px;width:300px">
  <div class="foot-h">Contact Us</div>
  <div style="margin-top:22px">
    <div class="contact-line"><svg width="14" height="18" viewBox="0 0 14 18"><path d="M7 0C3 0 0 3 0 7c0 5 7 11 7 11s7-6 7-11c0-4-3-7-7-7zm0 10a3 3 0 110-6 3 3 0 010 6z" fill="var(--blue)"/></svg><span>5830 E Larkspur Avenue,<br>Suite 2-140<br>Aurora, CO 80012</span></div>
    <div class="contact-line"><svg width="16" height="16" viewBox="0 0 24 24"><path d="M6.6 10.8a15 15 0 006.6 6.6l2.2-2.2c.3-.3.7-.4 1-.2 1.1.4 2.3.6 3.6.6.6 0 1 .4 1 1V20c0 .6-.4 1-1 1A17 17 0 013 4c0-.6.4-1 1-1h3.5c.6 0 1 .4 1 1 0 1.3.2 2.5.6 3.6.1.3 0 .7-.2 1z" fill="var(--blue)"/></svg><span>+1 888 555 0147</span></div>
    <div class="contact-line"><svg width="16" height="14" viewBox="0 0 16 14"><rect x="0" y="1" width="16" height="12" fill="var(--blue)"/><path d="M0 1l8 6 8-6" fill="none" stroke="#fff" stroke-width="1.3"/></svg><span>info@brightpathcoursecraft.example</span></div>
  </div>
</div>
<div class="abs map" role="img" aria-label="Street map showing the office location"></div>
<svg class="abs" style="left:912px;top:3690px" width="22" height="30" viewBox="0 0 14 18"><path d="M7 0C3 0 0 3 0 7c0 5 7 11 7 11s7-6 7-11c0-4-3-7-7-7zm0 10a3 3 0 110-6 3 3 0 010 6z" fill="#222"/></svg>

<nav class="abs foot-nav"><span>Home</span><span>Portfolio</span><span>Team &amp; Experience</span><span>Contact</span></nav>
<footer class="abs bottombar">© 2019 &nbsp;|&nbsp; www.companyname.com</footer>

</body>
</html>
```